Create a memorable Stationary for Security Software Company

Velbrantix is the worldwide leader in securing the Internet. Making Internet communications and critical data secure, reliable and available everywhere has been and continues to be our ongoing vision. We are committed to staying focused on real customer needs and to developing new and innovative security solutions that redefine the security landscape.

Industry/Entity Type

Internet

Font styles to use
Serif
Sans Serif
Script

Colors
0792cd
33a6d7
85cae6

```html
<!DOCTYPE html>
<html lang="en">
<head>
<meta charset="utf-8">
<title>Velbrantix Business Cards</title>
<link rel="stylesheet" href="https://fonts.googleapis.com/css2?family=Open+Sans:wght@400;600;700&display=swap">
<style>
  :root {
    --blue-deep: #0792cd;
    --blue-mid: #33a6d7;
    --blue-light: #85cae6;
    --ink-grey: #6f7478;
    --card-white: #ffffff;
    --card-shade: #eceeef;
    --backdrop: #e4e6e8;
  }
  html, body {
    margin: 0;
    width: 1200px;
    height: 780px;
    overflow: hidden;
    background: var(--backdrop);
    font-family: "Open Sans", Arial, sans-serif;
  }
  .canvas {
    position: relative;
    width: 1200px;
    height: 780px;
  }
  .card {
    position: absolute;
    width: 560px;
    height: 320px;
    border-radius: 16px;
    overflow: hidden;
    background: radial-gradient(ellipse at 50% 45%, var(--card-white) 40%, var(--card-shade) 100%);
    box-shadow: 0 10px 24px rgba(0,0,0,0.18);
  }
  .card--front { left: 50px; top: 70px; }
  .card--back { left: 590px; top: 390px; }
  .card__bands {
    position: absolute;
    inset: 0;
    width: 560px;
    height: 320px;
  }
  .brand {
    position: absolute;
    display: flex;
    align-items: center;
    gap: 12px;
    white-space: nowrap;
  }
  .brand__dot {
    width: 40px;
    height: 40px;
    border-radius: 50%;
    background: var(--blue-mid);
  }
  .brand__name {
    font-weight: 700;
    font-size: 30px;
    color: var(--blue-mid);
    letter-spacing: 0.2px;
  }
  .card--front .brand { left: 50%; top: 84px; transform: translateX(-50%); }
  .card--back .brand { left: 50%; top: 50%; transform: translate(-50%, -50%); }
  .contact {
    position: absolute;
    left: 50%;
    top: 164px;
    transform: translateX(-50%);
    color: var(--ink-grey);
    font-size: 12px;
    line-height: 1.7;
    white-space: nowrap;
  }
  .contact__name {
    color: var(--blue-deep);
    font-weight: 700;
    font-size: 20px;
    margin-bottom: 4px;
  }
  .contact__sep { color: var(--blue-deep); margin: 0 6px; }
  .contact__web { color: var(--blue-deep); }
  .address {
    position: absolute;
    left: 0;
    right: 0;
    top: 36px;
    text-align: center;
    color: var(--blue-deep);
    font-size: 12px;
    white-space: nowrap;
  }
</style>
</head>
<body>
<div class="canvas">
  <section class="card card--front">
    <svg class="card__bands" viewBox="0 0 560 320" aria-hidden="true">
      <defs>
        <linearGradient id="bandFront" x1="0" y1="0" x2="0" y2="1">
          <stop offset="0" stop-color="#33a6d7"/>
          <stop offset="1" stop-color="#0792cd"/>
        </linearGradient>
      </defs>
      <line x1="22" y1="0" x2="22" y2="320" stroke="#85cae6" stroke-width="2"/>
      <path d="M30 0 H110 Q80 160 110 320 H30 Z" fill="url(#bandFront)"/>
      <line x1="538" y1="0" x2="538" y2="320" stroke="#85cae6" stroke-width="2"/>
      <path d="M530 0 H450 Q480 160 450 320 H530 Z" fill="url(#bandFront)"/>
    </svg>
    <div class="brand">
      <span class="brand__dot"></span>
      <span class="brand__name">Velbrantix</span>
    </div>
    <div class="contact">
      <div class="contact__name">Employee Name</div>
      <div>P: 000 000 0000<span class="contact__sep">|</span>E: hello@velbrantix.com</div>
      <div class="contact__web">www.velbrantix.com</div>
    </div>
  </section>

  <section class="card card--back">
    <svg class="card__bands" viewBox="0 0 560 320" aria-hidden="true">
      <defs>
        <linearGradient id="bandBack" x1="0" y1="0" x2="0" y2="1">
          <stop offset="0" stop-color="#33a6d7"/>
          <stop offset="1" stop-color="#0792cd"/>
        </linearGradient>
      </defs>
      <line x1="22" y1="0" x2="22" y2="320" stroke="#85cae6" stroke-width="2"/>
      <path d="M30 0 H110 Q80 160 110 320 H30 Z" fill="url(#bandBack)"/>
      <line x1="538" y1="0" x2="538" y2="320" stroke="#85cae6" stroke-width="2"/>
      <path d="M530 0 H450 Q480 160 450 320 H530 Z" fill="url(#bandBack)"/>
    </svg>
    <div class="address">0000 Harbor Lane, 2nd Ste. Dunmere, Ohio 1234</div>
    <div class="brand">
      <span class="brand__dot"></span>
      <span class="brand__name">Velbrantix</span>
    </div>
  </section>
</div>
</body>
</html>
```